Etiketten für Deodorant in fester Form
Zielgruppe
Naturkosmetik
Aufgabenstellung
Dimension of the tube:
The height of the tube’s body is 53mm
The height of the lid is 20mm
The circular of the body is 126mm

```html
<!DOCTYPE html>
<html lang="fr">
<head>
<meta charset="utf-8">
<title>Déodorant solide – étiquette</title>
<link href="https://fonts.googleapis.com/css2?family=Figtree:wght@400&family=Noto+Sans+Arabic:wght@400&display=swap" rel="stylesheet">
<style>
  :root {
    --label-olive: #2b3a12;
    --label-ink: #ffffff;
  }
  html, body {
    margin: 0;
    padding: 0;
    width: 1200px;
    height: 800px;
    overflow: hidden;
    background: var(--label-olive);
  }
  .label {
    position: relative;
    width: 1200px;
    height: 800px;
    background: var(--label-olive);
    color: var(--label-ink);
    font-family: "Figtree", "Open Sans", sans-serif;
    font-size: 17.5px;
    line-height: 1;
  }
  .line {
    position: absolute;
    left: 0;
    width: 1200px;
    text-align: center;
    transform: translateY(-50%);
    white-space: nowrap;
  }
  .line.ar {
    font-family: "Noto Sans Arabic", sans-serif;
    font-size: 15.5px;
    direction: rtl;
  }
  .email { text-decoration: underline; }
  .bullet {
    position: absolute;
    left: 91px;
    top: 669px;
    width: 7px;
    height: 7px;
    border-radius: 50%;
    background: var(--label-ink);
  }
</style>
</head>
<body>
<main class="label">
  <div class="line" style="top:79px">Deodorant solide</div>
  <div class="line" style="top:103px">Au beurre de cacao</div>

  <div class="line ar" style="top:151px">مزيل العرق الصلب</div>
  <div class="line ar" style="top:175px">مع زبدة الكاكاو</div>

  <div class="line" style="top:221px">peau sensible</div>
  <div class="line ar" style="top:269px">البشرة الحساسة</div>

  <div class="line" style="top:316px">Application: poussez le stick d´en bas et appliquez le déodorant sous l´aisselle. Ne pas utiliser sur une peau irritée ou blessée.</div>
  <div class="line ar" style="top:340px">الاستخدام : ادفع العصا من الأسفل وضع مزيل العرق تحت الإبط</div>
  <div class="line ar" style="top:364px">.لا يستخدم على البشرة المتهيجة أوالمصابة</div>

  <div class="line" style="top:411px">Ingrédients: beurre de cacao, amidon de maïs, huile de coco, oxyde de zinc, cire d´abeille</div>
  <div class="line ar" style="top:435px">المكونات: زبدة الكاكاو ، نشا الذرة ، زيت جوز الهند ، أكسيد الزنك ، شمع العسل</div>

  <div class="line" style="top:483px">Sans huiles essentielles - Sans bicarbonate de soude - Sans aluminium - Sans alcool- Bio</div>
  <div class="line" style="top:507px">Lumeval Algerie</div>
  <div class="line" style="top:531px">12 Rue des Oliviers 31.000 Oran</div>
  <div class="line" style="top:555px"><span class="email">contact@lumeval.dz</span></div>

  <div class="line" style="top:601px">Date de Fabrication:</div>
  <div class="line" style="top:649px">Lot:</div>
  <span class="bullet"></span>
  <div class="line" style="top:673px">40g</div>
</main>
</body>
</html>
```